Standardization and redesign of graphics for a non-fiction book

For a book project, 11 graphics need to be visually unified so that all the graphics in the book are in the same style. The graphics must be created from scratch. Just new colors aren't enough. Some of the existing graphics are by other authors who own the copyright. Accordingly, the new graphics must be truly new. This is especially true for the "2 S-curves" graphic.

Target Market(s)

Manager Furniture Industry

Industry/Entity Type

Möbel

Colors
0054AA
0677BA
7BADD7
CADEEF
E8F1F8

```html
<!DOCTYPE html>
<html lang="de">
<head>
<meta charset="UTF-8">
<title>Einflussfaktoren Schweizer Wohnungseinrichtungsmarkt</title>
<link href="https://fonts.googleapis.com/css2?family=Poppins:wght@700&display=swap" rel="stylesheet">
<style>
  :root {
    --bg: #ffffff;
    --ring: #2ea6e8;
    --label: #666666;
    --chevron: #2ea6e8;
    --market-start: #29efee;
    --market-end: #15afd8;
    --market-text: #ffffff;
  }
  * { margin: 0; padding: 0; box-sizing: border-box; }
  html, body {
    width: 1200px;
    height: 1200px;
    overflow: hidden;
    background: var(--bg);
  }
  .diagram {
    position: relative;
    width: 1200px;
    height: 1200px;
    font-family: "Poppins", sans-serif;
    font-weight: 700;
  }
  .factor {
    position: absolute;
    left: 246px;
    width: 212px;
    height: 212px;
    border: 2px solid var(--ring);
    border-radius: 50%;
    display: flex;
    align-items: center;
    justify-content: center;
    text-align: center;
    color: var(--label);
    font-size: 26px;
    line-height: 28px;
  }
  .factor--macro { top: 226px; }
  .factor--trends { top: 493px; }
  .factor--business { top: 760px; }
  .chevron {
    position: absolute;
    left: 0;
    top: 0;
  }
  .market {
    position: absolute;
    left: 585px;
    top: 414px;
    width: 370px;
    height: 370px;
    border-radius: 50%;
    background: linear-gradient(160deg, var(--market-start) 0%, var(--market-end) 100%);
    display: flex;
    align-items: center;
    justify-content: center;
    text-align: center;
    color: var(--market-text);
    font-size: 26px;
    line-height: 28px;
  }
</style>
</head>
<body>
  <div class="diagram">
    <div class="factor factor--macro">makroöko-<br>nomisches<br>Umfeld</div>
    <div class="factor factor--trends">Mega-<br>trends</div>
    <div class="factor factor--business">neue<br>Geschäfts-<br>modelle</div>

    <svg class="chevron" width="1200" height="1200" viewBox="0 0 1200 1200" aria-hidden="true">
      <polygon points="490,570 505,555 550,599 505,643 490,629 520,599" fill="var(--chevron)"/>
    </svg>

    <div class="market">Schweizer<br>Wohnungs-<br>einrichtungsmarkt*</div>
  </div>
</body>
</html>
```